Business cards and stationary design

We just completed the design of our new logo and we need to print new business cards and letterhead for our nonprofit. We are looking for a fresh new design that shows off our new logo. On letterhead, we must have a column on the right or left to include our Board of Directors (up to 45 names) (see attachment)

Industry/Entity Type

Non-Profit

Contact Information for Business Card

Standard business card with name, title, Company name, mailing address phone numbers, email address and website. Tagline on back "Every neighbor deserves a roof"

Font styles to use
Sans Serif

Requirements
Must have
• include pertinent information above
• new logo
• fonts compatible with logo
• should use logo colors only
Nice to have
• tag lines

```html
<!DOCTYPE html>
<html lang="en">
<head>
<meta charset="utf-8">
<title>Hearthway Shelter Network – Business Card</title>
<link rel="stylesheet" href="https://fonts.googleapis.com/css2?family=Saira:wght@500;600;700&display=swap">
<style>
  :root {
    --teal: #0083a6;
    --red: #d7202a;
    --paper: #f8f8f8;
    --backdrop: #e4e4e4;
    --ink-grey: #555555;
    --white: #ffffff;
  }
  * { box-sizing: border-box; margin: 0; padding: 0; }
  html, body {
    width: 1200px; height: 582px; overflow: hidden;
    background: var(--backdrop);
    font-family: "Saira", Arial, sans-serif;
  }
  .canvas { position: relative; width: 1200px; height: 582px; }

  .card {
    position: absolute; top: 158px;
    width: 464px; height: 264px;
    background: var(--paper);
    overflow: hidden;
  }
  .card--front { left: 122px; }
  .card--back { left: 602px; }

  /* Front */
  .brand {
    position: absolute; left: 31px; top: 82px;
    display: flex; align-items: center; gap: 7px;
  }
  .brand__mark { width: 12px; height: 12px; background: var(--teal); flex: none; }
  .brand__name {
    font-weight: 600; font-size: 13.5px; line-height: 1; letter-spacing: 1px;
    color: var(--teal); text-transform: uppercase; white-space: nowrap;
  }
  .person { position: absolute; left: 31px; top: 124px; }
  .person__name {
    font-weight: 700; font-size: 21px; line-height: 1; color: var(--teal);
    text-transform: uppercase; white-space: nowrap;
  }
  .person__title {
    margin-top: 4px; font-weight: 600; font-size: 13.5px; line-height: 1;
    color: var(--red); text-transform: uppercase; letter-spacing: .3px;
  }
  .contact-band {
    position: absolute; left: 0; bottom: 0;
    width: 100%; height: 84px; background: var(--teal);
    color: var(--white); font-weight: 600; font-size: 10.5px;
  }
  .contact-list {
    position: absolute; left: 30px; top: 20px; list-style: none;
  }
  .contact-list li {
    display: flex; align-items: center; gap: 7px; height: 14.5px; white-space: nowrap;
  }
  .contact-list svg { width: 10px; height: 10px; fill: var(--white); flex: none; }
  .address {
    position: absolute; right: 32px; top: 20px;
    text-align: right; font-style: normal; line-height: 14.5px; white-space: nowrap;
  }
  .address__org { text-transform: uppercase; }

  /* Back */
  .back-brand {
    position: absolute; left: 0; right: 0; top: 114px;
    display: flex; justify-content: center; align-items: center; gap: 10px;
  }
  .back-brand__mark { width: 20px; height: 20px; background: var(--teal); flex: none; }
  .back-brand__name {
    font-weight: 600; font-size: 21px; line-height: 1; letter-spacing: 1.4px;
    color: var(--teal); text-transform: uppercase; white-space: nowrap;
  }
  .tagline {
    position: absolute; left: 0; right: 0; top: 222px;
    text-align: center; font-weight: 600; font-size: 11.5px; line-height: 1;
    letter-spacing: .6px; color: var(--ink-grey);
  }
</style>
</head>
<body>
<main class="canvas">

  <section class="card card--front" aria-label="Business card front">
    <div class="brand">
      <span class="brand__mark"></span>
      <span class="brand__name">Hearthway Shelter Network</span>
    </div>

    <div class="person">
      <p class="person__name">Daniel Reeve</p>
      <p class="person__title">CEO/Founder</p>
    </div>

    <div class="contact-band">
      <ul class="contact-list">
        <li>
          <svg viewBox="0 0 10 10" aria-hidden="true"><path d="M2.2 0.5 L3.6 2.6 L2.7 3.6 C3.3 5 4.9 6.6 6.4 7.3 L7.4 6.4 L9.5 7.8 L8.6 9.4 C4.5 9.4 0.6 5.5 0.6 1.4 Z"/></svg>
          <span>555 214 7730</span>
        </li>
        <li>
          <svg viewBox="0 0 10 10" aria-hidden="true"><path d="M0.5 2 H9.5 V8.2 H0.5 Z M1 2.4 L5 5.6 L9 2.4 V3.2 L5 6.4 L1 3.2 Z" fill-rule="evenodd"/></svg>
          <span>daniel@hearthway.org</span>
        </li>
        <li>
          <svg viewBox="0 0 10 10" aria-hidden="true"><circle cx="5" cy="5" r="4.5"/><path d="M3 3.2 L5 2.5 L5.8 4.2 L4.2 5.5 L5 7.5 L3.2 6.5 Z" fill="#0083a6"/></svg>
          <span>www.hearthway.org</span>
        </li>
      </ul>
      <address class="address">
        <span class="address__org">Hearthway Shelter Network</span><br>
        412 Birchwood Avenue<br>
        Juneau, Alaska 99801
      </address>
    </div>
  </section>

  <section class="card card--back" aria-label="Business card back">
    <div class="back-brand">
      <span class="back-brand__mark"></span>
      <span class="back-brand__name">Hearthway Shelter Network</span>
    </div>
    <p class="tagline">Every neighbor deserves a roof</p>
  </section>

</main>
</body>
</html>
```